Im open to ideas.. I was thinking on my business cards aswell as my logo. a place for my name. email. phone number and abn..

ive attched a file with my business logo. which i dont love the colours.. i was think a dark background with charcoal letters so something along those colour schumes but im open to ideas..

BRM Constructions

```html
<!DOCTYPE html>
<html lang="en">
<head>
<meta charset="utf-8">
<title>BRM Constructions – Business Cards</title>
<link href="https://fonts.googleapis.com/css2?family=Open+Sans:wght@400;600&display=swap" rel="stylesheet">
<style>
  :root {
    --page-bg: #ecebea;
    --card-light: #d4d4d4;
    --card-dark: #555555;
    --band-black: #1e1e1e;
    --band-rule: #e6e6e6;
    --brand-dark: #4a4a4a;
    --brand-muted: #8c8c8c;
    --text-light: #f2f2f2;
    --text-soft: #dcdcdc;
  }
  * { margin: 0; padding: 0; box-sizing: border-box; }
  html, body { width: 1200px; height: 900px; overflow: hidden; }
  body {
    position: relative;
    background: var(--page-bg);
    font-family: "Open Sans", Arial, sans-serif;
  }
  .card {
    position: absolute;
    overflow: hidden;
    box-shadow: 0 4px 14px rgba(0,0,0,0.18);
  }
  .card--front {
    left: 78px; top: 35px; width: 587px; height: 362px;
    background: var(--card-light);
  }
  .card--back {
    left: 388px; top: 505px; width: 567px; height: 352px;
    background: var(--card-dark);
  }
  .card__shapes { position: absolute; inset: 0; }
  .brand-name {
    position: absolute;
    font-weight: 600;
    white-space: nowrap;
    letter-spacing: 0.5px;
  }
  .card--front .brand-name {
    left: 0; right: 0; top: 108px;
    text-align: center;
    font-size: 44px;
    color: var(--brand-dark);
  }
  .card--back .brand-name {
    left: 38px; top: 158px;
    font-size: 30px;
    color: var(--brand-muted);
  }
  .abn {
    position: absolute;
    left: 35px; top: 211px;
    font-size: 14px;
    font-weight: 600;
    color: var(--text-light);
  }
  .contact-list {
    position: absolute;
    left: 35px; top: 265px;
    list-style: none;
  }
  .contact-list li {
    display: flex; align-items: center;
    height: 21px;
    font-size: 15px;
    color: var(--text-light);
  }
  .contact-list svg { width: 11px; height: 11px; margin-right: 7px; fill: var(--text-soft); }
  .person {
    position: absolute;
    right: 36px; top: 262px;
    text-align: right;
  }
  .person__name { font-size: 22px; font-weight: 600; color: var(--text-light); line-height: 1.2; }
  .person__role { font-size: 15px; color: var(--text-soft); }
</style>
</head>
<body>

<section class="card card--front">
  <svg class="card__shapes" viewBox="0 0 587 362" width="587" height="362" aria-hidden="true">
    <polygon points="0,235 372,235 412,200 587,200 587,362 0,362" fill="var(--card-dark)"/>
    <polygon points="0,208 402,208 376,235 0,235" fill="var(--band-black)"/>
    <polyline points="0,237 377,237 411,206" fill="none" stroke="var(--band-rule)" stroke-width="2"/>
  </svg>
  <div class="brand-name">BRM Constructions</div>
  <div class="abn">ABN:7654321</div>
  <ul class="contact-list">
    <li><svg viewBox="0 0 12 12"><path d="M1 4c0-2 2-3 5-3s5 1 5 3H8.5L8 3H4L3.5 4zM2 6l2-2h4l2 2v5H2z"/></svg>044-987 654 321</li>
    <li><svg viewBox="0 0 12 12"><path d="M0 2h12v8H0z M1 3l5 4 5-4" stroke="#555" stroke-width="0.8"/></svg>hello@brmbuild.com</li>
    <li><svg viewBox="0 0 12 12"><circle cx="6" cy="6" r="5.5"/></svg>www.brmbuild.com</li>
  </ul>
  <div class="person">
    <div class="person__name">Daniel Moore</div>
    <div class="person__role">Managing Director</div>
  </div>
</section>

<section class="card card--back">
  <div class="brand-name">BRM Constructions</div>
</section>

</body>
</html>
```